Road Construction Company needs business cards

We would like a new business card designed for our business.

We're a road construction company based in Qld, Australia.

Can the business card please have the following information on it.

Name: Warren Halbeck
Position: General Manager
Phone: 0472 915 348
Email: Warren.halbeck@tovrin.com.au
Address: 87 Marrow Ave, Pendlebay, QLD, 4023
Website: www.tovrin.com.au

Visually we'd like the card to be professional and simple.

Attached is our logo.

Our website is www.tovrin.com.au

Target Market(s)

Men aged 25-60

Contact Information for Business Card

As listed in project description

Font styles to use
Serif

Requirements
Must have
• Large logo on back of card

```html
<!DOCTYPE html>
<html lang="en">
<head>
<meta charset="utf-8">
<title>Tovrin – Business Card</title>
<link rel="stylesheet" href="https://fonts.googleapis.com/css2?family=Barlow+Condensed:wght@500;600;700&family=Montserrat:wght@400;500&display=swap">
<style>
  :root {
    --navy: #1254a3;
    --sky: #2aa6d8;
    --white: #ffffff;
    --stage: #2f3033;
    --stock-light: #e4e5e9;
    --stock-mid: #d3d5db;
  }
  * { margin: 0; padding: 0; box-sizing: border-box; }
  html, body { width: 1200px; height: 1200px; overflow: hidden; }
  body {
    background: var(--stage);
    position: relative;
    font-family: "Montserrat", Arial, sans-serif;
  }
  .card {
    position: absolute;
    left: 170px;
    width: 860px;
    height: 491px;
    overflow: hidden;
    box-shadow: 0 6px 18px rgba(0,0,0,0.35);
  }
  .card--front { top: 69px; background: var(--white); }
  .card--back { top: 640px; }

  .card__wave { position: absolute; inset: 0; width: 100%; height: 100%; }

  .identity { position: absolute; left: 56px; top: 46px; }
  .identity__name {
    font-family: "Barlow Condensed", "Arial Narrow", sans-serif;
    font-weight: 700;
    font-size: 44px;
    line-height: 1;
    color: var(--navy);
    letter-spacing: 0.5px;
  }
  .identity__role {
    font-family: "Barlow Condensed", "Arial Narrow", sans-serif;
    font-weight: 500;
    font-size: 22px;
    line-height: 1;
    margin-top: 2px;
    color: var(--sky);
    letter-spacing: 1.2px;
  }

  .brand-name {
    font-family: "Barlow Condensed", "Arial Narrow", sans-serif;
    font-weight: 700;
    color: var(--navy);
    text-transform: uppercase;
    line-height: 1;
  }
  .brand-name--front {
    position: absolute;
    right: 40px;
    top: 44px;
    font-size: 62px;
    letter-spacing: 3px;
  }

  .contact-list { position: absolute; left: 55px; top: 247px; list-style: none; }
  .contact-list__item {
    display: flex;
    align-items: center;
    height: 37px;
    margin-bottom: 17px;
    color: var(--white);
    font-size: 19.5px;
    font-weight: 400;
  }
  .contact-list__icon {
    width: 37px;
    height: 37px;
    border-radius: 8px;
    background: var(--white);
    margin-right: 11px;
    display: flex;
    align-items: center;
    justify-content: center;
    flex: none;
  }
  .contact-list__icon svg { width: 24px; height: 24px; }

  .card__texture {
    position: absolute;
    inset: 0;
    background:
      linear-gradient(90deg, transparent 40%, rgba(255,255,255,0.35) 46%, transparent 50%, rgba(255,255,255,0.3) 53%, transparent 59%),
      radial-gradient(ellipse at 50% 40%, var(--stock-light), var(--stock-mid));
  }
  .brand-name--back {
    position: absolute;
    left: 0; right: 0;
    top: 210px;
    text-align: center;
    font-size: 118px;
    letter-spacing: 8px;
  }
  .back-web {
    position: absolute;
    left: 0; right: 0;
    top: 429px;
    text-align: center;
    font-size: 19px;
    letter-spacing: 4px;
    color: var(--navy);
  }
</style>
</head>
<body>

<section class="card card--front">
  <svg class="card__wave" viewBox="0 0 972 555" preserveAspectRatio="none" aria-hidden="true">
    <path d="M0 215 C130 150 300 160 480 240 C660 320 850 380 972 292 V555 H0Z" fill="var(--navy)"/>
    <path d="M0 258 C130 195 300 200 480 275 C660 352 850 412 972 322 V555 H0Z" fill="var(--sky)"/>
    <path d="M0 287 C130 225 300 230 480 303 C660 380 850 438 972 352 V555 H0Z" fill="var(--navy)"/>
  </svg>

  <div class="identity">
    <h1 class="identity__name">WARREN HALBECK</h1>
    <p class="identity__role">GENERAL MANAGER</p>
  </div>

  <div class="brand-name brand-name--front">Tovrin</div>

  <ul class="contact-list">
    <li class="contact-list__item">
      <span class="contact-list__icon">
        <svg viewBox="0 0 24 24" fill="none" stroke="var(--navy)" stroke-width="2"><rect x="7" y="2" width="10" height="20" rx="2"/><circle cx="12" cy="18.5" r="0.8" fill="var(--navy)"/></svg>
      </span>
      0472 915 348
    </li>
    <li class="contact-list__item">
      <span class="contact-list__icon">
        <svg viewBox="0 0 24 24" fill="none" stroke="var(--navy)" stroke-width="1.8"><rect x="2.5" y="5" width="19" height="14" rx="1"/><path d="M2.5 5.5 12 13l9.5-7.5M2.5 18.5l7-6M21.5 18.5l-7-6"/></svg>
      </span>
      Warren.halbeck@tovrin.com.au
    </li>
    <li class="contact-list__item">
      <span class="contact-list__icon">
        <svg viewBox="0 0 24 24" fill="none" stroke="var(--navy)" stroke-width="1.5"><circle cx="12" cy="12" r="9.5"/><ellipse cx="12" cy="12" rx="4.5" ry="9.5"/><path d="M2.5 12h19M4 7h16M4 17h16M12 2.5v19"/></svg>
      </span>
      www.tovrin.com.au
    </li>
    <li class="contact-list__item">
      <span class="contact-list__icon">
        <svg viewBox="0 0 24 24"><path d="M12 2a7 7 0 0 0-7 7c0 5 7 12 7 12s7-7 7-12a7 7 0 0 0-7-7z" fill="var(--navy)"/><circle cx="12" cy="9" r="2.8" fill="var(--white)"/><ellipse cx="12" cy="22" rx="3" ry="0.8" fill="var(--navy)"/></svg>
      </span>
      87 Marrow Ave, Pendlebay, QLD, 4023
    </li>
  </ul>
</section>

<section class="card card--back">
  <div class="card__texture" role="img" aria-label="Faded photograph of an asphalt road with centre lines running into the distance"></div>
  <div class="brand-name brand-name--back">Tovrin</div>
  <p class="back-web">www.tovrin.com.au</p>
</section>

</body>
</html>
```